Wordpress Site Design for a Horror and Action Movie Production Company

We need a re-design/facelift of our website: https://k42t.pagecraft.io
The structure of the website could remain the same, but it needs to look and feel BETTER!

We would like the website coded in Wordpress so that it can be easily updated bu us, via adding new projects and new projects' info.

We specialize in Action, Horror, and Sci-Fi Genre. That being said, we don't want the website to look like it's a themed park with haunted houses. It should still be sharp and professional, as after all - it is a business for us!

Target Market(s)

Film Distribution Companies (B2B), as well as general audience that likes movies

Industry/Entity Type

Movie Production

Coding

Coded - Design and coding required

Number of Pages Required

5+ page

Font styles to use
Sans Serif

Colors

Designer to choose colors to be used in the design.

Requirements
Must have
• - PROJECTS page
• - Each PROJECT has a sub-page with project info/updates (up dates could be in a form of a WP post, ideally a template that we can use to update and create new PROJECT pages, with text, poster, and video link (trailer))
• - NEWS page that chronologically lists updates from all PROJECTS (could be done via WP blog)
• - HOME page would
Nice to have
• Should generally have a dark background.
• Websites we like as a reference of general approach and style:
• https://marbletoq.com
• https://velunpix.com (however this is very image-centric, and we might not have that much imagery at the moment)
• https://www.copperfieldechoandframe.com/other
• https://quennreels.com
Should not have
• We specialize in Action, Horror, and Sci-Fi Genre. That being said, we don't want the website to look like it's a themed park with haunted houses. It should still be sharp and professional, as after all - it is a business for us!

```html
<!DOCTYPE html>
<html lang="en">
<head>
<meta charset="utf-8">
<title>Kestrel 42 Media</title>
<link rel="stylesheet" href="https://fonts.googleapis.com/css2?family=Oswald:wght@500;600&family=Lato:wght@400;700&display=swap">
<style>
:root{
  --black:#000;
  --panel:#1b1b1b;
  --white:#fff;
  --muted:#d9d9d9;
  --accent:#e0111b;
  --line:#bdbdbd;
}
*{box-sizing:border-box;margin:0;padding:0}
html,body{width:1200px;height:3230px;overflow:hidden;background:var(--panel)}
body{position:relative;font-family:'Lato',sans-serif;color:var(--white)}
.abs{position:absolute}
.head{font-family:'Oswald',sans-serif;font-weight:600;letter-spacing:.5px}
.center{left:0;width:1200px;text-align:center}
.btn{position:absolute;border:2px solid var(--white);color:var(--white);font-size:14px;display:flex;align-items:center;justify-content:center}
.dot{position:absolute;width:30px;height:30px;border-radius:50%;border:1.5px solid var(--white)}
.dot.fill{background:var(--white)}

.site-header{left:0;top:0;width:1200px;height:122px;background:var(--black)}
.brand{left:82px;top:30px;width:204px;text-align:center}
.brand-name{font-family:'Oswald',sans-serif;font-weight:600;font-size:32px;letter-spacing:1px;line-height:1}
.brand-sub{font-size:11px;letter-spacing:5px;font-weight:700;margin-top:4px;border-bottom:2px solid var(--white);padding-bottom:6px}
.nav{top:54px;font-size:13px;font-weight:700}
.nav-active{border-bottom:2px solid var(--white);padding-bottom:10px}

.hero{left:0;top:122px;width:1200px;height:610px;background:radial-gradient(ellipse at 35% 40%,#8a5a45 0%,#5a3426 30%,#2b1712 60%,#120b09 100%)}
.hero-kicker{left:675px;top:346px;font-size:12px}
.hero-title{left:675px;top:362px;font-size:42px;line-height:50px;color:#e8e8e8}
.slider-dot{position:absolute;left:31px;width:8px;height:8px;border-radius:50%;background:var(--white)}

.about-text{left:290px;top:822px;width:630px;font-size:13.5px;line-height:17px;text-align:center}
.partner{font-family:'Oswald',sans-serif;font-weight:500;font-size:18px;line-height:23px}
.title{font-size:36px}

.poster{position:absolute}
.caption{font-family:'Oswald',sans-serif;font-size:14px}

.card{position:absolute;border:1.5px solid var(--line)}
.news-body{font-size:14px;line-height:17px}
.news-body a,.item a{color:var(--white);text-decoration:underline}
.item{position:absolute;left:781px;width:265px;font-size:13px;line-height:16px}
.item b{font-size:14px}
.thumb{position:absolute;left:632px;width:132px;height:111px}

.field{position:absolute;border:1.5px solid var(--line);font-size:14px;padding:10px 15px}

.footer-line{font-size:13px}
</style>
</head>
<body>

<!-- header -->
<header class="abs site-header">
  <div class="abs brand">
    <div class="brand-name">KESTREL 42</div>
    <div class="brand-sub">MEDIA</div>
  </div>
  <nav>
    <span class="abs nav nav-active" style="left:488px">Home</span>
    <span class="abs nav" style="left:562px">About</span>
    <span class="abs nav" style="left:639px">Projects</span>
    <span class="abs nav" style="left:728px">News</span>
    <span class="abs nav" style="left:800px">Partner</span>
    <span class="abs nav" style="left:884px">Contact</span>
  </nav>
  <span class="dot fill" style="left:966px;top:47px" aria-label="Social link"></span>
  <span class="dot" style="left:1007px;top:47px" aria-label="Social link"></span>
  <span class="dot" style="left:1048px;top:47px" aria-label="Social link"></span>
  <span class="dot" style="left:1089px;top:47px" aria-label="Social link"></span>
</header>

<!-- hero -->
<section class="abs hero" role="img" aria-label="Film still: close-up of a bearded man in warm low light"></section>
<span class="slider-dot" style="top:392px"></span>
<span class="slider-dot" style="top:406px"></span>
<span class="slider-dot" style="top:418px;background:none;border:1.5px solid #fff"></span>
<span class="slider-dot" style="top:432px"></span>
<span class="slider-dot" style="top:445px"></span>
<div class="abs hero-kicker head">WELCOME TO KESTREL 42 MEDIA INC</div>
<h1 class="abs hero-title head">HORROR &amp; ACTION<br>MOVIE</h1>
<div class="btn" style="left:675px;top:465px;width:197px;height:52px">Contact us</div>

<!-- section curves -->
<svg class="abs" style="left:0;top:660px" width="1200" height="2520" viewBox="0 660 1200 2520">
  <path d="M0 735 Q600 610 1200 735 V1120 Q600 1240 0 1120 Z" fill="#000"/>
  <path d="M0 1885 Q600 1790 1200 1885 V2470 Q600 2590 0 2470 Z" fill="#000"/>
  <path d="M0 2975 Q600 2880 1200 2975 V3180 H0 Z" fill="#000"/>
</svg>

<!-- about -->
<h2 class="abs center head title" style="top:728px">About us</h2>
<div class="abs" style="left:558px;top:792px;width:87px;height:2px;background:var(--white)"></div>
<p class="abs about-text">Kestrel 42 Media Inc (K42M) is a fresh brand of multi-media Visual Content, aimed at development of original Canadian content as well as servicing of foreign productions here at home, in Ontario, Canada.<br>K42M is a child of a partnership between two Canadian companies, which for years have been recognized as key brands in the Canadian media landscape:</p>
<div class="abs partner" style="left:400px;top:930px;width:182px;text-align:right">Corvid Lane<br>Entertainment Inc</div>
<div class="abs" style="left:601px;top:930px;width:2px;height:86px;background:var(--white)"></div>
<div class="abs partner" style="left:619px;top:930px;width:200px">Amber Nine<br>Entertainment Inc</div>
<div class="abs" style="left:524px;top:982px;width:58px;height:42px;background:#d8d8d8" role="img" aria-label="Partner badge"></div>
<div class="abs" style="left:619px;top:982px;width:94px;height:32px;background:#d8d8d8" role="img" aria-label="Partner badge"></div>
<div class="btn" style="left:503px;top:1059px;width:197px;height:52px">Read More</div>

<!-- projects -->
<h2 class="abs center head title" style="top:1218px">Projects</h2>
<div class="poster" style="left:0;top:1327px;width:334px;height:273px;background:linear-gradient(135deg,#6b7580,#3a3f46 60%,#8a2a2e)" role="img" aria-label="Project poster: tattooed hands over a face"></div>
<div class="poster" style="left:351px;top:1294px;width:514px;height:337px;background:linear-gradient(100deg,#cfc9bd 0%,#6e6357 35%,#2e2723 70%,#8c7260)" role="img" aria-label="Project poster: Iron Verdict, a boxer training with a heavy bag"></div>
<div class="poster" style="left:879px;top:1327px;width:321px;height:273px;background:linear-gradient(120deg,#2a2a2a,#5a1a1a 55%,#3a3a3a)" role="img" aria-label="Project poster: a figure in red with a saw blade"></div>
<svg class="abs" style="left:308px;top:1613px" width="28" height="22"><path d="M26 11H4M12 3L3 11l9 8" stroke="#fff" stroke-width="3" fill="none"/></svg>
<svg class="abs" style="left:878px;top:1613px" width="28" height="22"><path d="M2 11h22M16 3l9 8-9 8" stroke="#fff" stroke-width="3" fill="none"/></svg>
<div class="abs center caption" style="top:1651px">Iron Verdict</div>
<div class="abs center caption" style="top:1674px;color:var(--accent)">www.reelpreview.net</div>
<div class="btn" style="left:503px;top:1719px;width:197px;height:52px">View More</div>

<!-- news -->
<h2 class="abs center head title" style="top:1874px">Latest News</h2>
<div class="card" style="left:80px;top:1966px;width:507px;height:403px"></div>
<div class="abs" style="left:97px;top:1983px;width:475px;height:209px;background:linear-gradient(180deg,#5b5e7a,#2f2b35 60%,#1a1a1d)" role="img" aria-label="News photo: a film cast group on an ice rink"></div>
<div class="abs" style="left:110px;top:2163px;width:51px;height:41px;background:#4a4a4a;font-size:13px;text-align:center;line-height:16px;padding-top:4px">14<br>Oct</div>
<div class="abs news-body" style="left:100px;top:2224px;width:465px">What is Lorem Ipsum?<br><span style="display:block;margin-top:8px">Lorem Ipsum is simply dummy text of the printing and typesetting and Lorem Ipsum has been the industry's standard dummy text ever since the 1500s when an unknown printer took a galley.</span><a style="display:block;margin-top:18px">Read More</a></div>

<div class="card" style="left:613px;top:1966px;width:507px;height:403px"></div>
<div class="thumb" style="top:1983px;background:linear-gradient(135deg,#a86b8c,#4e2f4a)" role="img" aria-label="News thumbnail: portrait in purple light"></div>
<div class="thumb" style="top:2110px;background:linear-gradient(135deg,#8d8d8d,#3a3a3a)" role="img" aria-label="News thumbnail: dark grey film still"></div>
<div class="thumb" style="top:2237px;background:linear-gradient(135deg,#7a5a8e,#2a1d33)" role="img" aria-label="News thumbnail: horror film still"></div>
<div class="item" style="top:1983px"><b>Oct 14, 2019</b><br>What is Lorem Ipsum?<br>Lorem Ipsum is simply dummy text of the printing and typesetting and Lorem Ipsum text ever since the 1500s.<br><a>Read More</a></div>
<div class="item" style="top:2110px"><b>Oct 14, 2019</b><br>What is Lorem Ipsum?<br>Lorem Ipsum is simply dummy text of the printing and typesetting and Lorem Ipsum text ever since the 1500s.<br><a>Read More</a></div>
<div class="item" style="top:2237px"><b>Oct 14, 2019</b><br>What is Lorem Ipsum?<br>Lorem Ipsum is simply dummy text of the printing and typesetting and Lorem Ipsum text ever since the 1500s.<br><a>Read More</a></div>
<div class="abs" style="left:1099px;top:1981px;width:5px;height:368px;background:#bbb;border-radius:3px"></div>
<div class="abs" style="left:1093px;top:2013px;width:17px;height:17px;background:#bbb;border-radius:50%"></div>
<div class="btn" style="left:503px;top:2411px;width:197px;height:53px">View More</div>

<!-- contact -->
<h2 class="abs center head title" style="top:2550px">Contact us</h2>
<p class="abs center" style="top:2603px;font-size:14px">Lorem Ipsum is simply dummy the printing and typesetting industry.</p>
<div class="field" style="left:276px;top:2637px;width:317px;height:43px">Name*</div>
<div class="field" style="left:276px;top:2692px;width:317px;height:43px">Phone*</div>
<div class="field" style="left:276px;top:2750px;width:317px;height:43px">Email*</div>
<div class="field" style="left:606px;top:2637px;width:316px;height:156px">Message</div>
<div class="btn" style="left:505px;top:2814px;width:197px;height:51px">View More</div>

<!-- footer -->
<h3 class="abs center head" style="top:2958px;font-size:18px">K42M HEADQUARTERS</h3>
<p class="abs center footer-line" style="top:2993px">22-840 HARBOUR ROW, TORONTO, ON, M5T2L9, CANADA</p>
<p class="abs center footer-line" style="top:3018px">P : 00 555 010 2244 &nbsp;| &nbsp;E : info@kestrel42.com</p>
<h3 class="abs center head" style="top:3054px;font-size:18px">FOLLOW US OUR SOCIAL MEDIA</h3>
<span class="dot fill" style="left:499px;top:3090px" aria-label="Social link"></span>
<span class="dot" style="left:540px;top:3090px" aria-label="Social link"></span>
<span class="dot" style="left:581px;top:3090px" aria-label="Social link"></span>
<span class="dot" style="left:622px;top:3090px" aria-label="Social link"></span>
<span class="dot" style="left:662px;top:3090px" aria-label="Social link"></span>
<div class="abs" style="left:0;top:3160px;width:1200px;height:70px;background:var(--black);border-top:1px solid #555"></div>
<p class="abs center" style="top:3185px;font-size:14px">Copyright © 2019 KESTREL 42 MEDIA. All Right Reserve</p>

</body>
</html>
```